Harbor Wonder Hour - A magic website for a monthly modern magic show

Looking to build a website to promote my new monthly magic show

Sites like this. https://velvetloftshow.example/ https://sevencuriouscardsnight.example/

Target Market(s)

18-65 year old men and women who enjoy live entertainment especially magic

Industry/Entity Type

Entertainment

Coding

Coded - Design and coding required

Number of Pages Required

3 page

Colors

Designer to choose colors to be used in the design.

Requirements
Must have
• Wanting a wordpress site.
• Contact form, media section for photos and videos to be posted.
• A “reviews/testimonials” section.

```html
<!DOCTYPE html>
<html lang="en">
<head>
<meta charset="utf-8">
<title>Harbor Wonder Hour</title>
<link rel="stylesheet" href="https://fonts.googleapis.com/css2?family=Poppins:wght@300;500;600;700;800&display=swap">
<style>
  :root {
    --bg-deep: #1c1c20;
    --bg-mid: #2c2c31;
    --bg-light: #3a3a40;
    --text-main: #ffffff;
    --text-muted: #9a9a9e;
    --accent: #e07128;
  }
  * { margin: 0; padding: 0; box-sizing: border-box; }
  html, body { width: 1200px; height: 800px; overflow: hidden; }
  body { font-family: "Poppins", sans-serif; color: var(--text-main); background: var(--bg-deep); }
  .hero { position: relative; width: 1200px; height: 800px; overflow: hidden; }
  .hero-backdrop {
    position: absolute; inset: 0;
    background:
      radial-gradient(ellipse 55% 45% at 48% 32%, var(--bg-light) 0%, rgba(58,58,64,0) 70%),
      radial-gradient(ellipse 40% 50% at 80% 50%, #333338 0%, rgba(51,51,56,0) 70%),
      linear-gradient(160deg, var(--bg-mid) 0%, var(--bg-deep) 100%);
  }
  .brand { position: absolute; left: 44px; top: 40px; font-size: 17px; font-weight: 800; letter-spacing: 0.2px; line-height: 1; }
  .main-nav { position: absolute; right: 43px; top: 47px; display: flex; gap: 24px; }
  .main-nav a { color: var(--text-main); text-decoration: none; font-size: 11px; font-weight: 500; line-height: 1; }
  .intro-line { position: absolute; font-weight: 700; line-height: 1; letter-spacing: -1px; }
  .intro-greeting { left: 360px; top: 308px; font-size: 94px; color: var(--text-main); }
  .intro-name { left: 494px; top: 398px; font-size: 94px; color: var(--accent); }
  .intro-role { position: absolute; right: 366px; top: 494px; font-size: 15px; font-weight: 300; color: var(--text-muted); line-height: 1; }
  .social-list { position: absolute; left: 44px; top: 631px; list-style: none; display: flex; flex-direction: column; gap: 24px; }
  .social-list a { display: block; width: 18px; text-align: center; font-size: 7px; font-weight: 600; line-height: 13px; color: var(--text-main); text-decoration: none; }
  .social-list a.is-active { color: var(--accent); }
  .scroll-cue {
    position: absolute; left: 1143px; top: 676px;
    writing-mode: vertical-rl; font-size: 10px; font-weight: 600; letter-spacing: 0.4px; line-height: 1;
  }
</style>
</head>
<body>
  <main class="hero">
    <div class="hero-backdrop" role="img" aria-label="Dark moody photo of a rain puddle on paving stones reflecting a person walking"></div>

    <div class="brand">NAME</div>

    <nav class="main-nav">
      <a href="#tricks">TRICKS</a>
      <a href="#contact">CONTACT ME</a>
    </nav>

    <h1>
      <span class="intro-line intro-greeting">I AM</span>
      <span class="intro-line intro-name">MARLOW</span>
    </h1>
    <p class="intro-role">A MAGICIAN</p>

    <ul class="social-list">
      <li><a href="#">Orbit</a></li>
      <li><a href="#" class="is-active">Flick</a></li>
      <li><a href="#">Nexa</a></li>
      <li><a href="#">Frame</a></li>
    </ul>

    <div class="scroll-cue">SCROLL DOWN</div>
  </main>
</body>
</html>
```